Harborline Renewal Business Card Design

Professional and clean design. The design colors should flow with the logo. Two-sided card with the website on the back which is:

www.HarborlineRenewal.example.

"Specializing in Water Damage Restoration"

On the front I need the name, email, phone, and logo.

Name: Darnell Quisby
Email: Darnell@HarborlineRenewal.example
Phone: 555-318-2046 for now

I only have the Preview and Thumbnail right now but should have the source files uploaded within a day or two.

Target Market(s)

Flood victims, home owners with water damage from busted pipes etc...

Industry/Entity Type

Business

Contact Information for Business Card

Name: Darnell Quisby

Font styles to use
Serif
Sans Serif

Requirements
Must have
• Business Card Details Info

```html
<!DOCTYPE html>
<html lang="en">
<head>
<meta charset="utf-8">
<title>Harborline Renewal Business Card</title>
<link rel="stylesheet" href="https://fonts.googleapis.com/css2?family=Cinzel:wght@400;600&family=Open+Sans:wght@400&display=swap">
<style>
  :root {
    --sky: #57bfee;
    --ocean: #2a92d2;
    --brand: #3390cf;
    --ink: #1c1c1c;
    --text: #2b2b2b;
    --paper: #ffffff;
    --rule: #9a9a9a;
    --backdrop: #eeece8;
  }
  * { box-sizing: border-box; margin: 0; padding: 0; }
  html, body {
    width: 1200px; height: 982px; overflow: hidden;
    background: var(--backdrop);
  }
  .stage { position: relative; width: 1200px; height: 982px; }

  .card {
    position: absolute;
    width: 793px; height: 454px;
    border-radius: 44px;
    overflow: hidden;
  }

  /* Front */
  .card-front { left: 377px; top: 22px; background: var(--paper); box-shadow: 0 1px 3px rgba(0,0,0,.25); }
  .card-front .swoosh { position: absolute; inset: 0; }
  .holder { position: absolute; right: 28px; top: 30px; text-align: right; color: var(--paper); font-family: "Cinzel", serif; }
  .holder-name { font-size: 29px; font-weight: 400; letter-spacing: .5px; }
  .holder-title { font-size: 23px; letter-spacing: 2px; margin-top: 2px; }

  .brand-circle {
    position: absolute; left: 170px; top: 78px;
    width: 104px; height: 104px; border-radius: 50%;
    background: var(--brand);
  }
  .brand-name {
    position: absolute; left: 30px; top: 194px; width: 380px;
    text-align: center; color: var(--brand);
    font-family: "Cinzel", serif; font-weight: 600;
  }
  .brand-name .line-one { display: block; font-size: 50px; letter-spacing: 2px; line-height: 1.05; }
  .brand-name .line-two { display: block; font-size: 24px; letter-spacing: 6px; margin-top: 2px; }

  .contact { position: absolute; left: 38px; top: 336px; font-family: "Open Sans", sans-serif; font-size: 19px; color: var(--text); }
  .contact li { list-style: none; display: flex; align-items: center; height: 31px; }
  .contact svg { width: 16px; height: 16px; margin-right: 12px; flex: none; }
  .divider { position: absolute; left: 416px; top: 374px; width: 1.5px; height: 56px; background: var(--rule); }
  .address { position: absolute; left: 433px; top: 367px; font-family: "Open Sans", sans-serif; font-size: 19px; font-style: normal; color: var(--text); line-height: 31px; }

  /* Back */
  .card-back { left: 36px; top: 502px; background: var(--sky); }
  .back-circle {
    position: absolute; left: 296px; top: 40px;
    width: 200px; height: 200px; border-radius: 50%;
    background: var(--ink);
  }
  .back-name {
    position: absolute; left: 0; right: 0; top: 258px;
    text-align: center; color: var(--ink);
    font-family: "Cinzel", serif; font-weight: 600; font-size: 32px; letter-spacing: 2px;
  }
  .tagline {
    position: absolute; left: 0; right: 0; top: 352px;
    text-align: center; color: var(--ink);
    font-family: "Cinzel", serif; font-size: 22px; letter-spacing: 1.5px;
  }
  .back-web {
    position: absolute; left: 0; right: 0; top: 396px;
    text-align: center; color: var(--ink);
    font-family: "Open Sans", sans-serif; font-size: 18px;
  }
</style>
</head>
<body>
<main class="stage">

  <section class="card card-front" aria-label="Business card front">
    <svg class="swoosh" viewBox="0 0 793 454" preserveAspectRatio="none" aria-hidden="true">
      <path d="M0 0 H793 V232 C600 130 300 40 0 72 Z" fill="var(--sky)"/>
      <path d="M0 66 C300 30 600 120 793 255 V275 C600 150 300 50 0 78 Z" fill="var(--ocean)"/>
    </svg>

    <div class="holder">
      <p class="holder-name">Darnell Quisby</p>
      <p class="holder-title">Title</p>
    </div>

    <div class="brand-circle" aria-hidden="true"></div>
    <p class="brand-name"><span class="line-one">HARBORLINE</span><span class="line-two">RENEWAL</span></p>

    <ul class="contact">
      <li>
        <svg viewBox="0 0 16 16" aria-hidden="true"><circle cx="8" cy="8" r="7" fill="none" stroke="var(--brand)" stroke-width="1.4"/><path d="M6 4.5 L7.3 6.3 L6.5 7.3 C7 8.5 7.6 9.1 8.7 9.6 L9.7 8.8 L11.5 10 L10.6 11.5 C7.5 11 5 8.5 4.6 5.5 Z" fill="var(--brand)"/></svg>
        555-318-2046
      </li>
      <li>
        <svg viewBox="0 0 16 16" aria-hidden="true"><path d="M1 6 L8 2 L15 6 V14 H1 Z" fill="var(--brand)"/><path d="M1 6 L8 10 L15 6" fill="none" stroke="#fff" stroke-width="1.2"/></svg>
        Darnell@HarborlineRenewal.example
      </li>
      <li>
        <svg viewBox="0 0 16 16" aria-hidden="true"><g fill="none" stroke="var(--brand)" stroke-width="1.3"><circle cx="8" cy="8" r="7"/><ellipse cx="8" cy="8" rx="3" ry="7"/><path d="M1 8 H15 M2.5 4.5 H13.5 M2.5 11.5 H13.5"/></g></svg>
        www.HarborlineRenewal.example
      </li>
    </ul>
    <div class="divider" aria-hidden="true"></div>
    <address class="address">Street Name, City Name<br>Zipcode-12345</address>
  </section>

  <section class="card card-back" aria-label="Business card back">
    <div class="back-circle" aria-hidden="true"></div>
    <p class="back-name">HARBORLINE RENEWAL</p>
    <p class="tagline">Specializing in Water Damage Restoration</p>
    <p class="back-web">www.HarborlineRenewal.example</p>
  </section>

</main>
</body>
</html>
```